LEARN Business Skills so you can Earn a good living

size of the poster is 8”x 10.75" plus 0.25" bleed.
Please leave 1 inch on the bottoum for footer
I want a design a poster that will attract people's attention.
I appreciate a creative ad however the ad should not take away from being able to clearly read the text.
-I also appreciate a simple creative ad that is not too busy.
-you can use graphics, vectors, or pictures of real people.
-however, if you use real people it should be a white male that is wearing a white shirt and look like a professional person.

Target Market(s)

Potential young business people

Industry/Entity Type

education

Requirements
Must have
• easy to read the text
Nice to have
• I would like a "creative" simple ad that is easy to be read
Should not have
• pictures of women

```html
<!DOCTYPE html>
<html lang="en">
<head>
<meta charset="utf-8">
<title>Business Enrichment Course Poster</title>
<link href="https://fonts.googleapis.com/css2?family=DM+Sans:wght@400;500;700&family=Playfair+Display:wght@900&family=Dancing+Script:wght@600&display=swap" rel="stylesheet">
<style>
  :root {
    --stage: #8b8b8b;
    --paper: #ededee;
    --paper-edge: #e4e5e7;
    --navy: #233e80;
    --navy-deep: #1f356f;
    --royal: #2c55a3;
    --orange: #e8912d;
    --ink: #2a3550;
    --rule: #c9cbd0;
    --skyline: #dcdfe4;
  }
  * { margin: 0; padding: 0; box-sizing: border-box; }
  html, body {
    width: 1200px; height: 1200px; overflow: hidden;
    background: var(--stage);
  }
  .poster {
    position: absolute; left: 174px; top: 0;
    width: 852px; height: 1200px;
    background: linear-gradient(180deg, var(--paper) 0%, var(--paper-edge) 100%);
    overflow: hidden;
    font-family: "DM Sans", Arial, sans-serif;
  }
  .skyline {
    position: absolute; left: 0; top: 250px; width: 852px; height: 700px;
    background: radial-gradient(ellipse at 40% 45%, var(--skyline) 0%, rgba(220,223,228,0.4) 55%, rgba(237,237,238,0) 80%);
  }
  .brand-block {
    position: absolute; left: 295px; top: 0; width: 262px; height: 250px;
    background: var(--navy);
    border-bottom: 16px solid var(--orange);
    display: flex; align-items: center; justify-content: center;
  }
  .brand-name {
    color: #ffffff; font-weight: 700; font-size: 44px; letter-spacing: 1px;
  }
  .hero-art {
    position: absolute; left: 538px; top: 347px; width: 268px; height: 226px;
    background: linear-gradient(135deg, rgba(44,85,163,0.12) 0%, rgba(44,85,163,0.5) 100%);
    border-radius: 6px;
  }
  .title {
    position: absolute; left: 50px; top: 330px; z-index: 1;
    font-family: "Playfair Display", Georgia, serif; font-weight: 900;
    font-size: 79px; line-height: 83px; color: var(--royal);
    letter-spacing: -1px;
  }
  .tagline {
    position: absolute; left: 0; width: 852px; top: 622px; text-align: center;
    font-family: "Dancing Script", cursive; font-weight: 600;
    font-size: 46px; color: var(--orange);
  }
  .benefit {
    position: absolute; top: 729px; width: 230px; text-align: center;
  }
  .benefit-icon {
    width: 120px; height: 120px; margin: 0 auto;
    border-radius: 26px 26px 0 26px;
    background: linear-gradient(135deg, var(--navy-deep) 0%, var(--royal) 100%);
  }
  .benefit-label {
    margin-top: 12px; font-weight: 500; font-size: 24px; line-height: 32px; color: var(--ink);
  }
  .benefit--job { left: 17px; }
  .benefit--business { left: 291px; }
  .benefit--salary { left: 579px; }
  .divider {
    position: absolute; top: 735px; width: 1px; height: 194px; background: var(--rule);
  }
  .divider--one { left: 263px; }
  .divider--two { left: 552px; }
  .skills {
    position: absolute; left: 40px; width: 772px; top: 968px;
    text-align: center; font-size: 14.5px; line-height: 27px; color: var(--ink);
  }
  .skills .sep { color: var(--orange); margin: 0 3px; }
</style>
</head>
<body>
<main class="poster">
  <div class="skyline" role="img" aria-label="Faint photograph of a city skyline with a tall skyscraper"></div>

  <header class="brand-block">
    <span class="brand-name">SKILLRISE</span>
  </header>

  <div class="hero-art" role="img" aria-label="Illustration of a businessman in a white shirt working on a laptop while riding a rising blue arrow, with a briefcase beside him"></div>

  <h1 class="title">BUSINESS<br>ENRICHMENT<br>COURSE</h1>

  <p class="tagline">A proven success of helping people</p>

  <section class="benefit benefit--job">
    <div class="benefit-icon" role="img" aria-label="Icon of a job candidate with a star rating"></div>
    <p class="benefit-label">Get a<br>Quality Job</p>
  </section>

  <div class="divider divider--one"></div>

  <section class="benefit benefit--business">
    <div class="benefit-icon" role="img" aria-label="Icon of a growing plant with a trend badge"></div>
    <p class="benefit-label">Start/Grow<br>Your Business</p>
  </section>

  <div class="divider divider--two"></div>

  <section class="benefit benefit--salary">
    <div class="benefit-icon" role="img" aria-label="Icon of a rising chart line with sparkles"></div>
    <p class="benefit-label">Increase Your<br>Salary</p>
  </section>

  <p class="skills">
    Business Administration<span class="sep">|</span>Small Business Management<span class="sep">|</span>Finance<span class="sep">|</span>Investments<span class="sep">|</span>Computers<span class="sep">|</span>Accounting<span class="sep">|</span><br>
    Sales Marketing<span class="sep">|</span>Project Management Interviewing Skills<span class="sep">|</span>Business Law<span class="sep">|</span>Negotiation<span class="sep">|</span>Public Speaking<span class="sep">|</span><br>
    Import/Export<span class="sep">|</span>Information Technology<span class="sep">|</span>Distribution<span class="sep">|</span>Marketing<span class="sep">|</span>Ledgerly<span class="sep">|</span>Real Estate<span class="sep">|</span>Health Care<span class="sep">|</span><br>
    Management<span class="sep">|</span>Marketnest
  </p>
</main>
</body>
</html>
```